BOLD & MINIMALIST DESIGN NEEDED

We want a very bold but minimalistic business card design that is impactful and utilizes both sides of the business card. Our current logo is included for your use.

We want bold fonts and good use of negative space. We don't want the logo to overpower the design.

Target Market(s)

Professionals who are building new commercial buildings.

Industry/Entity Type

Construction

Contact Information for Business Card

Name, Title, email, office phone, cell phone, website

Font styles to use
Serif
Sans Serif

Requirements
Must have
• Bold design!

```html
<!DOCTYPE html>
<html lang="en">
<head>
<meta charset="utf-8">
<title>Ridgeline Build – Business Card</title>
<link href="https://fonts.googleapis.com/css2?family=Montserrat:wght@400;500;800&family=Poppins:wght@400;600&display=swap" rel="stylesheet">
<style>
  :root {
    --backdrop: #2b2b2b;
    --ink: #0a0a0a;
    --paper: #ffffff;
    --lime: #9fcd55;
    --muted: #d9d9d9;
  }
  * { margin: 0; padding: 0; box-sizing: border-box; }
  html, body { width: 1200px; height: 875px; overflow: hidden; }
  body {
    background: var(--backdrop);
    font-family: "Montserrat", sans-serif;
    position: relative;
  }
  .card {
    position: absolute;
    width: 620px;
    height: 354px;
    border-radius: 22px;
    overflow: hidden;
    box-shadow: 0 18px 40px rgba(0,0,0,.45);
  }
  .card--front { left: 90px; top: 48px; background: var(--ink); }
  .card--back  { left: 490px; top: 470px; background: var(--paper); }

  .wordmark {
    position: absolute;
    display: flex;
    align-items: center;
    gap: 14px;
    font-family: "Montserrat", sans-serif;
    font-weight: 800;
    letter-spacing: 1px;
    text-transform: uppercase;
  }
  .wordmark__mark { width: 26px; height: 26px; background: var(--lime); }
  .card--front .wordmark {
    left: 0; right: 0; top: 148px; justify-content: center;
    color: var(--paper); font-size: 44px;
  }
  .card--back .wordmark {
    left: 0; right: 0; top: 62px; justify-content: center;
    color: var(--ink); font-size: 40px;
  }

  .band { position: absolute; }
  .band--contact {
    left: 300px; right: 0; top: 160px; height: 110px;
    background: var(--ink);
    padding: 14px 0 0 22px;
  }
  .band--identity {
    left: 0; width: 300px; top: 210px; height: 100px;
    background: var(--lime);
    text-align: right;
    padding: 18px 22px 0 0;
    color: var(--paper);
  }
  .person__name {
    font-family: "Poppins", sans-serif;
    font-weight: 600;
    font-size: 26px;
    line-height: 1.15;
  }
  .person__title {
    font-family: "Poppins", sans-serif;
    font-weight: 400;
    font-size: 14px;
  }
  .contact-list { list-style: none; }
  .contact-list li {
    display: flex; align-items: center; gap: 10px;
    color: var(--paper);
    font-size: 13.5px;
    font-weight: 500;
    line-height: 21px;
  }
  .contact-list svg { width: 14px; height: 14px; flex: none; }
</style>
</head>
<body>

  <section class="card card--front" aria-label="Card front">
    <div class="wordmark"><span class="wordmark__mark"></span>Ridgeline Build</div>
  </section>

  <section class="card card--back" aria-label="Card back">
    <div class="wordmark"><span class="wordmark__mark"></span>Ridgeline Build</div>

    <div class="band band--contact">
      <ul class="contact-list">
        <li>
          <svg viewBox="0 0 16 16" aria-hidden="true"><path fill="var(--lime)" d="M3.6 1.5l2.2 2.6-1.3 1.7c.8 1.9 2.3 3.4 4.2 4.2l1.7-1.3 2.6 2.2-1.2 2.2C6.6 14.8 1.2 9.4 1.4 2.7z"/></svg>
          (555) 214-0387
        </li>
        <li>
          <svg viewBox="0 0 16 16" aria-hidden="true"><rect x="2" y="6" width="12" height="8" rx="1.5" fill="var(--lime)"/><path d="M1 5.5c4-3.5 10-3.5 14 0l-2 1.5H3z" fill="var(--lime)"/></svg>
          1-800-555-0142
        </li>
        <li>
          <svg viewBox="0 0 16 16" aria-hidden="true"><rect x="1.5" y="3.5" width="13" height="9" rx="1" fill="var(--lime)"/><path d="M2 4l6 5 6-5" stroke="var(--ink)" stroke-width="1.3" fill="none"/></svg>
          info@ridgelinebuild.com
        </li>
        <li>
          <svg viewBox="0 0 16 16" aria-hidden="true"><circle cx="8" cy="8" r="6.5" fill="var(--lime)"/><path d="M1.5 8h13M8 1.5c-3 3.5-3 9.5 0 13M8 1.5c3 3.5 3 9.5 0 13" stroke="var(--ink)" stroke-width="1" fill="none"/></svg>
          www.ridgelinebuild.com
        </li>
      </ul>
    </div>

    <div class="band band--identity">
      <p class="person__name">Daniel Brooks</p>
      <p class="person__title">CEO &amp; Founder</p>
    </div>
  </section>

</body>
</html>
```